Calvanto Group Real Estate Company business cards

New business card design, we are generally happy with the basic layout of the existing front of business card, (feel free to change) but require a head shot photo on the back side.

http://www.calvanto.com.au/

Attached logos, and existing business card

------------------------------

Target Market(s)

Real estate

Industry/Entity Type

Real Estate

Contact Information for Business Card

Standard size double sided

Font styles to use
Other font styles liked:
• Futura

Requirements
Must have
• Photo head shot on the back side
Nice to have
• yes
Should not have
• No

```html
<!DOCTYPE html>
<html lang="en">
<head>
<meta charset="utf-8">
<title>Calvanto Group – Business Cards</title>
<link rel="stylesheet" href="https://fonts.googleapis.com/css2?family=Gelasio:wght@400;700&display=swap">
<style>
  :root {
    --backdrop: #26272a;
    --card-white: #ffffff;
    --card-shade: #eeeeee;
    --brand-purple: #2f1f66;
    --brand-orange: #e3830f;
    --brand-orange-light: #f0a550;
    --text-light: #ffffff;
    --photo-light: #d9dadc;
    --photo-dark: #4a5060;
  }
  * { margin: 0; padding: 0; box-sizing: border-box; }
  html, body {
    width: 1200px;
    height: 873px;
    overflow: hidden;
    background: var(--backdrop);
  }
  .card-sheet {
    position: relative;
    width: 1200px;
    height: 873px;
    display: flex;
    align-items: center;
    justify-content: center;
    gap: 40px;
  }
  .card {
    width: 540px;
    height: 309px;
    border-radius: 4px;
    overflow: hidden;
    box-shadow: 0 12px 30px rgba(0, 0, 0, 0.5);
  }
  .card svg { display: block; width: 100%; height: 100%; }
  .serif { font-family: 'Gelasio', Georgia, serif; }
  .wordmark { font-weight: 700; font-size: 34px; }
  .wordmark--purple { fill: var(--brand-purple); }
  .wordmark--orange { fill: var(--brand-orange); }
  .welcome-title { fill: var(--brand-orange); font-size: 21px; }
  .welcome-line { fill: var(--brand-purple); font-size: 19px; }
  .person-name { fill: var(--text-light); font-weight: 700; font-size: 18px; }
  .person-role { fill: var(--text-light); font-size: 12px; }
  .contact-line { fill: var(--text-light); font-size: 13px; }
  .contact-icon { fill: none; stroke: var(--brand-orange-light); stroke-width: 1.4; }
  .social-box { fill: var(--card-shade); }
</style>
</head>
<body>
<main class="card-sheet">

  <!-- Front side: welcome message -->
  <section class="card card--welcome" aria-label="Card side with welcome message">
    <svg viewBox="0 0 540 309" xmlns="http://www.w3.org/2000/svg">
      <defs>
        <linearGradient id="paper" x1="0" y1="0" x2="0" y2="1">
          <stop offset="0" stop-color="#ffffff"/>
          <stop offset="1" stop-color="#ececec"/>
        </linearGradient>
      </defs>
      <rect class="card-base" width="540" height="309" fill="url(#paper)"/>
      <path class="wave-light" fill="var(--brand-orange-light)"
            d="M0,240 C120,238 220,215 300,160 C380,105 450,70 540,58 L540,309 L0,309Z"/>
      <path class="wave-orange" fill="var(--brand-orange)"
            d="M0,258 C120,256 230,232 310,178 C390,124 460,92 540,80 L540,309 L0,309Z"/>
      <path class="wave-purple" fill="var(--brand-purple)"
            d="M0,282 C130,280 245,255 325,200 C400,150 465,118 540,106 L540,309 L0,309Z"/>
      <text class="serif welcome-title" x="70" y="138">Welcome to Calvanto Group!</text>
      <text class="serif welcome-line" x="92" y="166">Let us show you property</text>
      <text class="serif wordmark wordmark--orange" x="515" y="232" text-anchor="end">calvanto</text>
    </svg>
  </section>

  <!-- Back side: contact details and head shot -->
  <section class="card card--contact" aria-label="Card side with contact details">
    <svg viewBox="0 0 540 309" xmlns="http://www.w3.org/2000/svg">
      <defs>
        <linearGradient id="paper-b" x1="0" y1="0" x2="0" y2="1">
          <stop offset="0" stop-color="#ffffff"/>
          <stop offset="1" stop-color="#ececec"/>
        </linearGradient>
        <linearGradient id="headshot-tone" x1="0" y1="0" x2="0" y2="1">
          <stop offset="0" stop-color="var(--photo-light)"/>
          <stop offset="1" stop-color="var(--photo-dark)"/>
        </linearGradient>
      </defs>
      <rect class="card-base" width="540" height="309" fill="url(#paper-b)"/>
      <path class="wave-light" fill="var(--brand-orange-light)"
            d="M0,190 C140,190 260,175 340,140 C420,105 480,85 540,82 L540,309 L0,309Z"/>
      <path class="wave-orange" fill="var(--brand-orange)"
            d="M0,206 C140,206 265,192 345,156 C425,120 485,100 540,98 L540,309 L0,309Z"/>
      <path class="wave-purple" fill="var(--brand-purple)"
            d="M0,226 C145,226 275,212 355,176 C430,142 488,120 540,118 L540,309 L0,309Z"/>

      <text class="serif wordmark wordmark--purple" x="32" y="82">Calvanto Group</text>

      <circle cx="440" cy="88" r="64" fill="var(--card-shade)"/>
      <circle class="headshot" cx="440" cy="88" r="58" fill="url(#headshot-tone)"
              role="img" aria-label="Head shot photo of the director"/>

      <text class="serif person-name" x="440" y="184" text-anchor="middle">Daniel Tran</text>
      <text class="serif person-role" x="440" y="199" text-anchor="middle">Director</text>

      <g class="social-links" aria-label="Social profiles">
        <rect class="social-box" x="413" y="218" width="16" height="16" rx="2"/>
        <rect class="social-box" x="433" y="218" width="16" height="16" rx="2"/>
        <rect class="social-box" x="453" y="218" width="16" height="16" rx="2"/>
      </g>

      <g class="contact-list">
        <rect class="contact-icon" x="24" y="244" width="7" height="11" rx="1.5"/>
        <text class="serif contact-line" x="42" y="254">0412-555-308</text>

        <rect class="contact-icon" x="23" y="264" width="10" height="7"/>
        <path class="contact-icon" d="M23,264 L28,268 L33,264"/>
        <text class="serif contact-line" x="42" y="272">daniel.tran@calvanto.com.au</text>

        <circle class="contact-icon" cx="26" cy="288" r="2.6"/>
        <circle class="contact-icon" cx="31" cy="284" r="2.6"/>
        <text class="serif contact-line" x="42" y="291">www.calvanto.com.au</text>
      </g>
    </svg>
  </section>

</main>
</body>
</html>
```